Quick Straightforward Billboard Redesign

- Design billboard sized for 10 foot' x 36' foot width live area size and please include bleeds 6" around all sides
- Exact blue color match is imperative in headline, logo, phone number bubble or wherever used. C-83 / M-45 / Y-1 / K-0-
- What I hope to illustrate is that our company offers the best porch screening in the area area, in regards to quality, expertise, durability, storms proof, but we do not build screen porches.
- Current board is attached below from previous designer, and as you can see sizing was off, white space on edges make it appear to be sized incorrectly.
- I also attached my own little mock up idea well well if it helps, favorite image, logo, headline, etc and ideas perhaps on expanding or making this better?

Thanks so much!

Target Market(s)

Drivers and passengers, Southeastern NC, are of immense new construction and high end homes.

Industry/Entity Type

Construction

Colors
0054AA
0677BA
7BADD7
CADEEF
E8F1F8

Requirements
Must have
• Blue color matching
Nice to have
• Design spins or other thoughts on my little mock up

```html
<!DOCTYPE html>
<html lang="en">
<head>
<meta charset="utf-8">
<title>Tidewater Screens Billboard</title>
<link href="https://fonts.googleapis.com/css2?family=Oswald:wght@400;500;600;700&display=swap" rel="stylesheet">
<style>
  :root {
    --brand-blue: #0054AA;
    --brand-blue-mid: #0677BA;
    --brand-green: #14B357;
    --ink: #2a2a2a;
    --white: #ffffff;
    --stage: #3b3b3b;
  }
  * { margin: 0; padding: 0; box-sizing: border-box; }
  html, body {
    width: 1200px; height: 432px; overflow: hidden;
    background: var(--stage);
    font-family: "Oswald", "Arial Narrow", sans-serif;
  }
  .billboard {
    position: absolute; left: 0; top: 37px;
    width: 1200px; height: 357px;
    background: var(--white);
    overflow: hidden;
  }
  .scene-photo {
    position: absolute; left: 440px; top: 0; width: 760px; height: 357px;
    background:
      linear-gradient(90deg, #fff 0%, rgba(255,255,255,0.85) 14%, rgba(255,255,255,0) 34%),
      linear-gradient(180deg, #eef1f2 0%, #cfe3f2 22%, #9cc6e6 36%, #6e9a56 48%, #8fb46a 56%, #d7d2c6 64%, #c9c1b3 100%);
  }
  .headline {
    position: absolute; left: 49px; top: 16px;
    font-weight: 600; font-size: 68px; line-height: 61px;
    letter-spacing: -0.5px;
  }
  .headline .line-blue { color: var(--brand-blue); display: block; }
  .headline .line-green { color: var(--brand-green); display: block; }
  .features { position: absolute; left: 0; top: 160px; }
  .feature {
    position: absolute; width: 100px; text-align: center;
    color: var(--ink); font-size: 20px; font-weight: 400;
  }
  .feature svg { display: block; margin: 0 auto 6px; }
  .no-build {
    position: absolute; left: 419px; top: 162px; width: 95px; height: 92px;
    background: var(--brand-green); color: var(--white);
    border-radius: 6px 28px 28px 6px;
    padding: 10px 0 0 13px;
    font-size: 17px; line-height: 19px; font-weight: 500;
  }
  .brand {
    position: absolute; left: 47px; top: 283px;
    display: flex; align-items: center; gap: 12px;
    color: var(--brand-blue); font-weight: 600; font-size: 40px; line-height: 1;
  }
  .brand .mark { width: 26px; height: 26px; background: var(--brand-blue); }
  .phone {
    position: absolute; left: 441px; top: 271px; width: 316px; height: 52px;
    background: var(--brand-blue); border-radius: 0 22px 22px 0;
    display: flex; align-items: center; gap: 8px; padding-left: 12px;
    color: var(--white); font-weight: 600; font-size: 47px;
  }
  .phone svg { flex: none; }
  .award {
    position: absolute; left: 930px; top: 28px; width: 270px; height: 91px;
  }
  .award svg { position: absolute; left: 0; top: 0; }
  .award-text {
    position: absolute; left: 106px; top: 13px;
    color: var(--white); font-weight: 600; font-size: 19px; line-height: 20px;
  }
</style>
</head>
<body>
<main class="billboard">
  <div class="scene-photo" role="img" aria-label="Covered lakeside patio with wicker lounge chairs, a ceiling fan and a black fence facing a pond"></div>

  <h1 class="headline">
    <span class="line-blue">Screen Your&nbsp; Porch.</span>
    <span class="line-green">build for the coast.</span>
  </h1>

  <section class="features">
    <div class="feature" style="left:30px">
      <svg width="70" height="70" viewBox="0 0 70 70"><circle cx="35" cy="35" r="33" fill="none" stroke="var(--brand-green)" stroke-width="2"/><circle cx="35" cy="35" r="29" fill="var(--brand-blue)"/><circle cx="35" cy="40" r="12" fill="none" stroke="#fff" stroke-width="2"/><path d="M30 45v-8h3l3-6c2 0 2 2 1 5h5v3l-2 6z" fill="none" stroke="#fff" stroke-width="1.6"/><path d="M25 22l1 2 2 .3-1.5 1.4.4 2-1.9-1-1.9 1 .4-2L22 24.3l2-.3zM35 18l1 2 2 .3-1.5 1.4.4 2-1.9-1-1.9 1 .4-2L32 20.3l2-.3zM45 22l1 2 2 .3-1.5 1.4.4 2-1.9-1-1.9 1 .4-2L42 24.3l2-.3z" fill="none" stroke="#fff" stroke-width="1.1"/></svg>
      Quality
    </div>
    <div class="feature" style="left:122px">
      <svg width="70" height="70" viewBox="0 0 70 70"><circle cx="35" cy="35" r="33" fill="none" stroke="var(--brand-green)" stroke-width="2"/><circle cx="35" cy="35" r="29" fill="var(--brand-blue)"/><circle cx="29" cy="36" r="8" fill="none" stroke="#fff" stroke-width="2" stroke-dasharray="4 2"/><circle cx="29" cy="36" r="3" fill="none" stroke="#fff" stroke-width="1.6"/><circle cx="41" cy="42" r="6" fill="none" stroke="#fff" stroke-width="1.6"/><path d="M38 42l2 2 4-4" fill="none" stroke="#fff" stroke-width="1.6"/><path d="M37 30v-8c2 0 3 2 2 6h6v6" fill="none" stroke="#fff" stroke-width="1.6"/></svg>
      Expertise
    </div>
    <div class="feature" style="left:215px">
      <svg width="70" height="70" viewBox="0 0 70 70"><circle cx="35" cy="35" r="33" fill="none" stroke="var(--brand-green)" stroke-width="2"/><circle cx="35" cy="35" r="29" fill="var(--brand-blue)"/><path d="M22 44l12-12 4 4-12 12z M34 32l8-8c3 0 6 2 7 5l-5-1-6 8" fill="none" stroke="#fff" stroke-width="1.8" stroke-linejoin="round"/><path d="M20 30a16 16 0 0 1 14-12" fill="none" stroke="#fff" stroke-width="1.2" stroke-dasharray="2 2"/></svg>
      Durability
    </div>
    <div class="feature" style="left:307px">
      <svg width="70" height="70" viewBox="0 0 70 70"><circle cx="35" cy="35" r="33" fill="none" stroke="var(--brand-green)" stroke-width="2"/><circle cx="35" cy="35" r="29" fill="var(--brand-blue)"/><path d="M24 38h22a6 6 0 0 0 0-12 9 9 0 0 0-17-2 7 7 0 0 0-5 14z" fill="none" stroke="#fff" stroke-width="1.8"/><path d="M38 38l-4 7h4l-3 6" fill="none" stroke="#fff" stroke-width="1.8"/><path d="M25 42l-2 4M30 42l-2 4M27 48l-1 2" stroke="#fff" stroke-width="1.6"/></svg>
      Storms Proof
    </div>
  </section>

  <div class="no-build">WE DO<br>NOT BUILD<br>SCREEN<br>PORCHES</div>

  <div class="brand"><span class="mark"></span><span class="brand-name">TIDEWATER SCREENS</span></div>

  <div class="phone">
    <svg width="36" height="36" viewBox="0 0 36 36"><rect width="36" height="36" rx="8" fill="#fff"/><path d="M13 8c-2 1-4 3-3 7 1 5 6 11 11 13 3 1 5-1 6-3l-4-3-2 2c-3-1-6-5-7-8l2-2z" fill="var(--brand-blue)"/></svg>
    <span>555.014.2288</span>
  </div>

  <div class="award">
    <svg width="270" height="91" viewBox="0 0 270 91"><polygon points="42,0 270,0 270,91 42,91 0,45.5" fill="var(--brand-green)"/><polygon points="56,0 270,0 270,91 56,91 16,45.5" fill="var(--brand-blue)"/><g fill="none" stroke="#fff" stroke-width="2"><path d="M58 18h32v14a16 16 0 0 1-32 0z"/><path d="M58 22h-7c0 9 4 14 9 15M90 22h7c0 9-4 14-9 15"/><path d="M74 48v10M66 58h16v6H66z"/><path d="M74 26l2 4 4 .5-3 3 1 4-4-2-4 2 1-4-3-3 4-.5z"/></g></svg>
    <div class="award-text">THE BEST<br>PORCH SCREENING<br>IN THE AREA</div>
  </div>
</main>
</body>
</html>
```